Teach English in China Website Redesign Needed

We recruit native English speakers from the US, UK, etc. who want to teach English as a foreign language in schools in China. Our target customer is college educated, age 22-28 and they love to travel. We prefer designs with bright colors and lots of photos. We want to keep all the text on our current homepage, BrightLanternPost.com. We are open to changing our logo. A competitor's page that we like is pinemeadowtutors.com because of their bright colors, photos and use of white space. We are happy to give you a dofollow link and design credit on our homepage. The use of included photos is optional. We need at least a home page design and a standard blog post design.
Target Market(s)
Our target customer is college educated, age 22-28 and they love to travel. Half of our customers are kindergarten teachers. Half of our customers are male.
Logo Text
Bright Lantern Post
Requirements
Must have
- Bright colors
Should not have
- Our homepage must not look crowded. Use white space effectively.

```html
<!DOCTYPE html>
<html lang="en">
<head>
<meta charset="utf-8">
<title>Bright Lantern Post – Teach English in China</title>
<link href="https://fonts.googleapis.com/css2?family=Open+Sans:wght@400;600;700;800&display=swap" rel="stylesheet">
<style>
:root{
  --red:#e01e1e;
  --red-dark:#c01515;
  --ink:#222;
  --text:#555;
  --muted:#888;
  --line:#e3e3e3;
  --band:#efefef;
  --card:#f2f2f2;
  --white:#fff;
  --gold:#f4b400;
}
*{box-sizing:border-box;margin:0;padding:0}
html,body{width:1200px;height:5217px;overflow:hidden}
body{font-family:'Open Sans',Arial,sans-serif;color:var(--text);background:var(--white);font-size:13px;line-height:1.6}
a{color:inherit;text-decoration:none}
ul{list-style:none}
.wrap{width:940px;margin:0 auto;position:relative}
.photo{display:block}
section,header,footer{position:relative;overflow:hidden}
.section-title{font-size:27px;font-weight:600;color:var(--ink);text-align:center;line-height:1.2}
.btn-red{display:inline-block;background:var(--red);color:var(--white);font-weight:700;font-size:14px;letter-spacing:.5px;padding:12px 22px;border-radius:2px}
.pager{display:flex;gap:4px}
.pager span{width:22px;height:22px;border:1px solid #ccc;display:flex;align-items:center;justify-content:center;background:#fff}

/* header */
.site-header{height:132px}
.site-header .wrap{display:flex;justify-content:space-between;height:132px}
.brand{display:flex;align-items:center;gap:10px;font-size:26px;font-weight:800;color:var(--red);line-height:1}
.brand i{width:16px;height:16px;background:var(--red);display:block}
.head-right{padding-top:38px;text-align:right}
.head-top{display:flex;align-items:center;gap:26px;justify-content:flex-end}
.phone{display:flex;align-items:center;gap:6px;font-size:17px;font-weight:600;color:var(--ink)}
.search{width:218px;height:32px;border:1px solid #ccc;display:flex;align-items:center;justify-content:space-between;padding:0 10px;color:#aaa;font-size:12px}
.main-nav{display:flex;gap:30px;justify-content:flex-end;margin-top:18px;font-size:13px;font-weight:600;color:var(--ink)}
.main-nav .active{color:var(--red)}

/* hero */
.hero{height:477px;border-bottom:4px solid var(--red)}
.hero .photo{position:absolute;inset:0;background:linear-gradient(180deg,#8a9aa8 0%,#c9cfd4 35%,#8d5a3a 60%,#5a4a3a 85%,#3e3a34 100%)}
.slide-arrow{position:absolute;top:225px;width:26px;height:26px;border-radius:50%;background:rgba(255,255,255,.8);display:flex;align-items:center;justify-content:center}
.slide-arrow.left{left:22px}.slide-arrow.right{right:22px}

/* intro */
.intro{height:1033px;padding-top:80px;text-align:center}
.intro-lead{font-size:14px;color:var(--ink);width:640px;margin:14px auto 0;line-height:1.6}
.city-grid{display:grid;grid-template-columns:repeat(3,300px);column-gap:20px;row-gap:28px;margin-top:42px}
.city-card .photo{height:202px}
.city-card h3{color:var(--red);font-size:18px;font-weight:400;margin-top:16px}
.city-card p{font-size:11px;color:var(--muted);line-height:1.5;margin-top:6px;padding:0 14px}
.intro .btn-red{margin-top:46px}

/* testimonials */
.testimonials{height:334px;background:var(--band);padding-top:68px}
.testimonials .head{display:flex;justify-content:space-between;align-items:center}
.testimonials h2{font-size:27px;font-weight:600;color:var(--ink)}
.quote-row{display:grid;grid-template-columns:repeat(3,300px);column-gap:20px;margin-top:28px}
.quote-card{background:var(--white);border:1px solid var(--line);padding:14px 16px 14px 48px;position:relative;font-size:11px;color:var(--muted);line-height:1.6;height:150px}
.quote-card::before{content:"\201C";position:absolute;left:16px;top:6px;font-size:40px;color:#bbb;font-family:Georgia,serif}
.quote-by{display:flex;justify-content:flex-end;align-items:center;gap:8px;margin-top:8px;font-size:11px;color:var(--ink)}
.quote-by small{color:var(--muted)}
.stars{color:var(--gold);font-size:10px;letter-spacing:1px;display:block}
.avatar{width:30px;height:30px;background:linear-gradient(135deg,#c8a890,#7a6a5a)}
.gap-band{height:76px}

/* video */
.video-band{height:400px}
.video-band .photo{position:absolute;inset:0;background:linear-gradient(90deg,#6f7a2a 0%,#a6a838 30%,#c9b25a 55%,#7d8a3a 80%,#4c5a22 100%)}
.video-copy{position:absolute;left:130px;top:138px;color:var(--white)}
.video-copy h2{font-size:29px;font-weight:700;line-height:1.25;width:420px}
.ghost-row{display:flex;gap:12px;margin-top:16px}
.btn-ghost{border:1px solid rgba(255,255,255,.8);padding:6px 14px;font-size:12px;font-weight:600;display:flex;align-items:center;gap:6px}

/* locations */
.locations{height:435px;padding-top:72px;text-align:center;border-bottom:1px solid var(--line)}
.locations .sub{font-size:15px;color:var(--ink);margin-top:10px}
.loc-row{display:flex;justify-content:center;gap:97px;margin-top:24px}
.loc-item .photo{width:160px;height:160px;border-radius:50%}
.loc-item .apply{width:160px;height:160px;border-radius:50%;background:#3a3a3a;color:var(--white);font-weight:700;font-size:20px;display:flex;align-items:center;justify-content:center}
.loc-item span{display:block;color:var(--red);font-size:14px;margin-top:10px}

/* jobs */
.jobs{height:817px;padding-top:76px}
.job-grid{display:grid;grid-template-columns:repeat(4,216px);column-gap:25px;row-gap:50px;margin-top:28px}
.job-card{background:var(--card);height:278px;text-align:center}
.job-card .photo{height:170px}
.job-card h3{color:var(--red);font-size:17px;font-weight:600;margin-top:14px;line-height:1.2}
.job-card p{font-size:10px;color:var(--muted);margin-top:6px}
.job-card .more{display:inline-block;font-size:9px;font-weight:700;color:var(--ink);border-bottom:1px solid var(--ink);margin-top:16px}

/* faq */
.faq{height:226px;background:var(--band);padding-top:38px;text-align:center}
.faq .q{font-size:12px;font-weight:600;color:var(--ink);margin-top:10px}
.faq .a{font-size:11px;color:var(--muted);line-height:1.6;margin-top:8px}
.faq-arrow{position:absolute;top:100px}
.faq-arrow.left{left:28px}.faq-arrow.right{right:28px}

/* blog */
.blog{height:539px;padding-top:64px}
.blog .head{display:flex;justify-content:space-between;align-items:center}
.blog h2{font-size:27px;font-weight:600;color:var(--ink)}
.post-grid{display:grid;grid-template-columns:440px 440px;column-gap:60px;row-gap:45px;margin-top:22px}
.post{display:flex;background:var(--card);height:146px}
.post .photo{width:146px;flex:none}
.post-body{padding:12px 16px}
.post h3{font-size:14px;font-weight:600;color:var(--ink);line-height:1.3}
.post time{font-size:12px;color:var(--ink);display:block;margin-top:2px}
.post p{font-size:10px;color:var(--muted);margin-top:8px;line-height:1.6}
.post p b{color:var(--ink)}

/* cta */
.cta{height:400px;text-align:center}
.cta .photo{position:absolute;inset:0;background:linear-gradient(180deg,#3a3d44 0%,#5b5f66 35%,#6b5d4a 65%,#3e3428 100%)}
.cta-copy{position:relative;padding-top:130px;color:var(--white)}
.cta-copy h2{font-size:29px;font-weight:700;line-height:1.25}
.cta-copy .btn-red{margin-top:16px}

/* footer */
.site-footer{height:157px;padding-top:52px}
.foot-cols{display:flex}
.foot-cols h4{font-size:17px;font-weight:600;color:var(--ink)}
.foot-list{font-size:9px;color:var(--text);margin-top:8px;line-height:1.75}
.foot-list li::before{content:"";display:inline-block;width:4px;height:4px;background:var(--red);border-radius:50%;margin-right:6px;vertical-align:middle}
.col-links{width:168px}.col-cities{width:197px}.col-jobs{width:327px}
.job-cols{display:flex;gap:40px}
.newsletter .field{width:190px;height:30px;border:1px solid #ccc;margin-top:10px;display:flex;align-items:center;justify-content:space-between;padding:0 8px;font-size:9px;color:#aaa}
.newsletter small{display:block;font-size:9px;margin-top:8px}
.social{display:flex;gap:6px;margin-top:4px}
.social i{width:18px;height:18px;border-radius:50%;background:var(--red);display:block}
.bottom-bar{height:191px;background:var(--band);border-top:1px solid var(--line)}
.bottom-bar .wrap{display:flex;justify-content:space-between;padding-top:28px}
.bottom-left{display:flex;align-items:center;gap:18px}
.bottom-left .brand{font-size:18px;color:var(--ink)}
.bottom-left .brand i{background:var(--ink);width:12px;height:12px}
.bottom-left p{font-size:9px;color:var(--muted);line-height:1.5}
.bottom-right{text-align:right;font-size:9px;color:var(--muted)}
.bottom-right .phone{justify-content:flex-end;font-size:18px;margin-top:6px}
</style>
</head>
<body>

<header class="site-header">
  <div class="wrap">
    <a class="brand" href="#"><i></i>Bright Lantern Post</a>
    <div class="head-right">
      <div class="head-top">
        <span class="phone"><svg width="14" height="14" viewBox="0 0 24 24"><path fill="#222" d="M6.6 10.8a15 15 0 0 0 6.6 6.6l2.2-2.2a1 1 0 0 1 1-.25 11.4 11.4 0 0 0 3.6.6 1 1 0 0 1 1 1V20a1 1 0 0 1-1 1A17 17 0 0 1 3 4a1 1 0 0 1 1-1h3.5a1 1 0 0 1 1 1c0 1.25.2 2.45.6 3.6a1 1 0 0 1-.25 1z"/></svg>555-014-2327</span>
        <div class="search">Search<svg width="12" height="12" viewBox="0 0 24 24"><circle cx="10" cy="10" r="7" fill="none" stroke="#444" stroke-width="2.5"/><path d="M15 15l6 6" stroke="#444" stroke-width="2.5"/></svg></div>
      </div>
      <nav class="main-nav">
        <a class="active" href="#">Home</a><a href="#">Available Jobs</a><a href="#">Apply Online</a><a href="#">Blog</a><a href="#">FAQ</a>
      </nav>
    </div>
  </div>
</header>

<section class="hero">
  <div class="photo" role="img" aria-label="Traditional Chinese temple with red pillars and curved tiled roofs below misty mountains"></div>
  <span class="slide-arrow left"><svg width="10" height="10" viewBox="0 0 10 10"><path d="M7 1L3 5l4 4" fill="none" stroke="#333" stroke-width="1.5"/></svg></span>
  <span class="slide-arrow right"><svg width="10" height="10" viewBox="0 0 10 10"><path d="M3 1l4 4-4 4" fill="none" stroke="#333" stroke-width="1.5"/></svg></span>
</section>

<section class="intro">
  <div class="wrap">
    <h1 class="section-title">Teach English in China</h1>
    <p class="intro-lead">Want to teach English in China? Do you enjoy teaching children or adults? Would you like the adventure of teaching in China for a year? Then we have the perfect job for you!</p>
    <div class="city-grid">
      <article class="city-card"><div class="photo" role="img" aria-label="Lit pagoda reflected in a lake at night" style="height:202px;background:linear-gradient(180deg,#1a2a5a,#b8402a 55%,#1a1a30)"></div><h3>Beijing &amp; Shanghai</h3><p>Aenean egestas leo aliquam, consectetur orci a, sodales ipsum. Fusce rhoncus ligula vel lectus interdum, eget tincidunt leo dignissim.</p></article>
      <article class="city-card"><div class="photo" role="img" aria-label="Round temple hall under a deep blue sky" style="height:202px;background:linear-gradient(180deg,#1c3f8a,#3a5fae 55%,#6a2a2a)"></div><h3>Beijing &amp; Shanghai</h3><p>Aenean egestas leo aliquam, consectetur orci a, sodales ipsum. Fusce rhoncus ligula vel lectus interdum, eget tincidunt leo dignissim.</p></article>
      <article class="city-card"><div class="photo" role="img" aria-label="Red palace gate with an arched opening at dusk" style="height:202px;background:linear-gradient(180deg,#7a1010,#c0501c 55%,#3a0a0a)"></div><h3>Fuzhou</h3><p>Aenean egestas leo aliquam, consectetur orci a, sodales ipsum. Fusce rhoncus ligula vel lectus interdum, eget tincidunt leo dignissim.</p></article>
      <article class="city-card"><div class="photo" role="img" aria-label="City skyline with a tall tower across the river" style="height:202px;background:linear-gradient(180deg,#9cc4e4,#6f8ca4 60%,#4a5a66)"></div><h3>China</h3><p>Aenean egestas leo aliquam, consectetur orci a, sodales ipsum. Fusce rhoncus ligula vel lectus interdum, eget tincidunt leo dignissim.</p></article>
      <article class="city-card"><div class="photo" role="img" aria-label="Dancers in costume performing on stage" style="height:202px;background:linear-gradient(180deg,#5a3a6a,#a070a0 50%,#e0c0d0)"></div><h3>Shenzhen</h3><p>Aenean egestas leo aliquam, consectetur orci a, sodales ipsum. Fusce rhoncus ligula vel lectus interdum, eget tincidunt leo dignissim.</p></article>
      <article class="city-card"><div class="photo" role="img" aria-label="Red temple columns with a carved dragon statue" style="height:202px;background:linear-gradient(135deg,#3a3a3a,#a01818 50%,#d04030)"></div><h3>Nanjing</h3><p>Aenean egestas leo aliquam, consectetur orci a, sodales ipsum. Fusce rhoncus ligula vel lectus interdum, eget tincidunt leo dignissim.</p></article>
    </div>
    <a class="btn-red" href="#">VIEW JOB BOARD</a>
  </div>
</section>

<section class="testimonials">
  <div class="wrap">
    <div class="head"><h2>Testimonials</h2><div class="pager"><span><svg width="8" height="8" viewBox="0 0 10 10"><path d="M7 1L3 5l4 4" fill="none" stroke="#666" stroke-width="1.5"/></svg></span><span><svg width="8" height="8" viewBox="0 0 10 10"><path d="M3 1l4 4-4 4" fill="none" stroke="#666" stroke-width="1.5"/></svg></span></div></div>
    <div class="quote-row">
      <div><blockquote class="quote-card">Mauris quis sodales enim, semper ultrices massa. Pellentesque risus dolor, tristique vel facilisis ac, laoreet et elit. Fusce id augue et metus cursus pretium. Ut nec lectus porttitor, porttitor nibh vel, tempus lorem.</blockquote><div class="quote-by"><span>Mark Dale, <small>City name</small><span class="stars">★★★★★</span></span><span class="avatar" role="img" aria-label="Reviewer portrait"></span></div></div>
      <div><blockquote class="quote-card">Mauris quis sodales enim, semper ultrices massa. Pellentesque risus dolor, tristique vel facilisis ac, laoreet et elit. Fusce id augue et metus cursus pretium. Ut nec lectus porttitor, porttitor nibh vel, tempus lorem.</blockquote><div class="quote-by"><span>Mark Dale, <small>City name</small><span class="stars">★★★★★</span></span><span class="avatar" role="img" aria-label="Reviewer portrait"></span></div></div>
      <div><blockquote class="quote-card">Mauris quis sodales enim, semper ultrices massa. Pellentesque risus dolor, tristique vel facilisis ac, laoreet et elit. Fusce id augue et metus cursus pretium. Ut nec lectus porttitor, porttitor nibh vel, tempus lorem.</blockquote><div class="quote-by"><span>Mark Dale, <small>City name</small><span class="stars">★★★★★</span></span><span class="avatar" role="img" aria-label="Reviewer portrait"></span></div></div>
    </div>
  </div>
</section>
<div class="gap-band"></div>

<section class="video-band">
  <div class="photo" role="img" aria-label="Smiling young teacher outdoors against a blurred green and yellow background"></div>
  <div class="video-copy">
    <h2>Quisque fringilla ipsum tortor sed malesuada elit</h2>
    <div class="ghost-row">
      <a class="btn-ghost" href="#"><svg width="10" height="10" viewBox="0 0 10 10"><path d="M2 1l7 4-7 4z" fill="#fff"/></svg>Play This Video</a>
      <a class="btn-ghost" href="#"><svg width="10" height="10" viewBox="0 0 10 10"><rect x="1" y="1" width="8" height="8" fill="none" stroke="#fff"/></svg>View All Testimonials</a>
    </div>
  </div>
</section>

<section class="locations">
  <div class="wrap">
    <h2 class="section-title">Locations to Teach English in China</h2>
    <p class="sub">Morbi a lobortis odio, in dignissim orci. Lorem ipsum dolor sit amet, consectetur adipiscing elit.</p>
    <div class="loc-row">
      <div class="loc-item"><div class="photo" role="img" aria-label="Shanghai skyline" style="background:linear-gradient(180deg,#8ab4d8,#4a6a8a)"></div><span>Shanghai</span></div>
      <div class="loc-item"><div class="apply">APPLY NOW</div><span>Shenzhen</span></div>
      <div class="loc-item"><div class="photo" role="img" aria-label="Beijing gate tower" style="background:linear-gradient(180deg,#4a7ac0,#8a2a2a)"></div><span>Beijing</span></div>
      <div class="loc-item"><div class="photo" role="img" aria-label="Guangzhou city lights at night" style="background:linear-gradient(180deg,#2a2050,#8a4a9a)"></div><span>Guangzhou</span></div>
    </div>
  </div>
</section>

<section class="jobs">
  <div class="wrap">
    <h2 class="section-title">Job Types</h2>
    <div class="job-grid">
      <article class="job-card"><div class="photo" role="img" aria-label="Kindergarten class" style="background:linear-gradient(135deg,#d84a2a,#3a6ab0)"></div><h3>Kindergarten</h3><p>Pellentesque libero velit, accumsan</p><a class="more" href="#">VIEW MORE</a></article>
      <article class="job-card"><div class="photo" role="img" aria-label="Students in a language school" style="background:linear-gradient(135deg,#c8c8c8,#3a5a9a)"></div><h3>Language Schools</h3><p>Pellentesque libero velit, accumsan</p><a class="more" href="#">VIEW MORE</a></article>
      <article class="job-card"><div class="photo" role="img" aria-label="Public school students in uniform" style="background:linear-gradient(135deg,#8a2a3a,#4a3a5a)"></div><h3>Public Schools</h3><p>Pellentesque libero velit, accumsan</p><a class="more" href="#">VIEW MORE</a></article>
      <article class="job-card"><div class="photo" role="img" aria-label="University graduates" style="background:linear-gradient(135deg,#6a7a4a,#2a2a2a)"></div><h3>University</h3><p>Pellentesque libero velit, accumsan</p><a class="more" href="#">VIEW MORE</a></article>
      <article class="job-card"><div class="photo" role="img" aria-label="Adult learners at a laptop" style="background:linear-gradient(135deg,#e8e4e0,#8a7a6a)"></div><h3>Adult</h3><p>Pellentesque libero velit, accumsan</p><a class="more" href="#">VIEW MORE</a></article>
      <article class="job-card"><div class="photo" role="img" aria-label="Business meeting" style="background:linear-gradient(135deg,#b0b4b8,#3a3e44)"></div><h3>Business English</h3><p>Pellentesque libero velit, accumsan</p><a class="more" href="#">VIEW MORE</a></article>
      <article class="job-card"><div class="photo" role="img" aria-label="Directors in an office" style="background:linear-gradient(135deg,#d0d0cc,#5a6068)"></div><h3>Director of Studies</h3><p>Pellentesque libero velit, accumsan</p><a class="more" href="#">VIEW MORE</a></article>
      <article class="job-card"><div class="photo" role="img" aria-label="Children in yellow shirts" style="background:linear-gradient(135deg,#f0c030,#c07a2a)"></div><h3>Donec mauris</h3><p>Pellentesque libero velit, accumsan</p><a class="more" href="#">VIEW MORE</a></article>
    </div>
  </div>
</section>

<section class="faq">
  <div class="wrap">
    <h2 class="section-title">FAQ</h2>
    <p class="q">Pellentesque libero velit, accumsan ac venenatis ut, lacinia eu arcu. Nunc a tellus tincidunt, malesuada metus a, mattis elit?</p>
    <p class="a">Sed vitae semper turpis mollis turpis. Vestibulum consequat molestie sodales. Morbi lacus leo, ultrices eleifend sit arcu. In placerat nisl faucibus facilisis. Integer justo ligula, lobortis vel imperdiet vel, ornare lacinia ut dolor. Aliquam ultrices purus a lorem tempus, sed suscipit urna sollicitudin. Aenean ligula nisl, faucibus eu cursus lacus eu ante. Praesent facilisis enim nulla, vel lacinia nulla luctus vitae.</p>
  </div>
  <span class="faq-arrow left"><svg width="14" height="24" viewBox="0 0 14 24"><path d="M12 2L2 12l10 10" fill="none" stroke="#999" stroke-width="2"/></svg></span>
  <span class="faq-arrow right"><svg width="14" height="24" viewBox="0 0 14 24"><path d="M2 2l10 10L2 22" fill="none" stroke="#999" stroke-width="2"/></svg></span>
</section>

<section class="blog">
  <div class="wrap">
    <div class="head"><h2>Blog</h2><div class="pager"><span><svg width="8" height="8" viewBox="0 0 10 10"><path d="M7 1L3 5l4 4" fill="none" stroke="#666" stroke-width="1.5"/></svg></span><span><svg width="8" height="8" viewBox="0 0 10 10"><path d="M3 1l4 4-4 4" fill="none" stroke="#666" stroke-width="1.5"/></svg></span></div></div>
    <div class="post-grid">
      <article class="post"><div class="photo" role="img" aria-label="Garden path with lanterns" style="background:linear-gradient(135deg,#4a6a2a,#c0a040)"></div><div class="post-body"><h3>Curabitur lacinia semper nisl</h3><time>31 MAR, 2017</time><p>Sed eget sollicitudin nulla. Donec fermentum blandit dui sed ornare. Nullam viverra ipsum, in imperdiet fermentum eget purus at ligula. <b>More</b></p></div></article>
      <article class="post"><div class="photo" role="img" aria-label="Graduate in cap and gown" style="background:linear-gradient(135deg,#2a3a6a,#b0c0d0)"></div><div class="post-body"><h3>Curabitur lacinia semper nisl</h3><time>31 MAR, 2017</time><p>Sed eget sollicitudin nulla. Donec fermentum blandit dui sed ornare. Nullam viverra ipsum, in imperdiet fermentum eget purus at ligula. <b>More</b></p></div></article>
      <article class="post"><div class="photo" role="img" aria-label="Students studying together" style="background:linear-gradient(135deg,#d0d0d0,#3a4a6a)"></div><div class="post-body"><h3>Curabitur lacinia semper nisl</h3><time>31 MAR, 2017</time><p>Sed eget sollicitudin nulla. Donec fermentum blandit dui sed ornare. Nullam viverra ipsum, in imperdiet fermentum eget purus at ligula. <b>More</b></p></div></article>
      <article class="post"><div class="photo" role="img" aria-label="Teacher with a young student" style="background:linear-gradient(135deg,#8a7a6a,#2a2a3a)"></div><div class="post-body"><h3>Curabitur lacinia semper nisl</h3><time>31 MAR, 2017</time><p>Sed eget sollicitudin nulla. Donec fermentum blandit dui sed ornare. Nullam viverra ipsum, in imperdiet fermentum eget purus at ligula. <b>More</b></p></div></article>
    </div>
  </div>
</section>

<section class="cta">
  <div class="photo" role="img" aria-label="Great Wall winding over hills under a stormy sky with red autumn leaves"></div>
  <div class="cta-copy">
    <h2>Quisque fringilla ipsum tortor<br>sed malesuada elit</h2>
    <a class="btn-red" href="#">VIEW JOB BOARD</a>
  </div>
</section>

<footer class="site-footer">
  <div class="wrap foot-cols">
    <div class="col-links"><h4>Links</h4><ul class="foot-list"><li>Home</li><li>Available Jobs</li><li>Apply Online</li><li>Blog</li><li>FAQ</li></ul></div>
    <div class="col-cities"><h4>Cities</h4><ul class="foot-list"><li>Beijing &amp; Shanghai</li><li>Fuzhou</li><li>China</li><li>Shenzhen</li><li>Nanjing</li></ul></div>
    <div class="col-jobs"><h4>Job Types</h4><div class="job-cols"><ul class="foot-list"><li>Kindergarten</li><li>Language Schools</li><li>Public Schools</li><li>University</li><li>Adult</li></ul><ul class="foot-list"><li>Business English</li><li>Director of Studies</li><li>Donec mauris</li></ul></div></div>
    <div class="newsletter"><h4>Newsletter Subscribe</h4><div class="field">Email Address<svg width="12" height="10" viewBox="0 0 12 10"><rect x=".5" y=".5" width="11" height="9" fill="none" stroke="#444"/><path d="M.5 .5L6 5l5.5-4.5" fill="none" stroke="#444"/></svg></div><small>Follow us on</small><div class="social"><i></i><i></i><i></i><i></i><i></i><i></i><i></i><i></i></div></div>
  </div>
</footer>

<div class="bottom-bar">
  <div class="wrap">
    <div class="bottom-left"><span class="brand"><i></i>Bright Lantern Post</span><p>Copyright © 2017 Company name<br>All rights reserved</p></div>
    <div class="bottom-right">
      <p>© Avery Holt, Director, 42 Harbor Lane, Maple Ridge, Oregon 97000</p>
      <span class="phone"><svg width="14" height="14" viewBox="0 0 24 24"><path fill="#222" d="M6.6 10.8a15 15 0 0 0 6.6 6.6l2.2-2.2a1 1 0 0 1 1-.25 11.4 11.4 0 0 0 3.6.6 1 1 0 0 1 1 1V20a1 1 0 0 1-1 1A17 17 0 0 1 3 4a1 1 0 0 1 1-1h3.5a1 1 0 0 1 1 1c0 1.25.2 2.45.6 3.6a1 1 0 0 1-.25 1z"/></svg>555-014-2327</span>
    </div>
  </div>
</div>

</body>
</html>
```